Website Design - TallyPorchHelpers.net

PLEASE CHECK WORD DOCUMENT ATTACHED FOR WEBSITE FLOW.

Target Market(s)

REAL ESTATE AGENTS ARE THE TARGET MARKET

Industry/Entity Type

Real Estate

Coding

Coded - Design and coding required

Number of Pages Required

4 page

Colors

Designer to choose colors to be used in the design.

Requirements
Must have
• WE LIKE RED LOGO ATTACHED
Nice to have
• PLEASE CHECK WORD DOCUMENT ATTACHED FOR WEBSITE FLOW.
Should not have

```html
<!DOCTYPE html>
<html lang="en">
<head>
<meta charset="utf-8">
<title>Tally Porch Helpers</title>
<link href="https://fonts.googleapis.com/css2?family=Roboto:ital,wght@0,400;0,500;0,700;0,900;1,400&family=Roboto+Condensed:wght@700&display=swap" rel="stylesheet">
<style>
:root{
  --red:#e3101f;
  --navy:#221d80;
  --ink:#1c1c1c;
  --grey:#6b6b6b;
  --soft:#9a9a9a;
  --paper:#ffffff;
  --mist:#eeeded;
  --night:#1a1a1a;
  --line:#e6e6e6;
  --hero-top:#6f7468;
  --hero-bottom:#4f7a32;
}
*{box-sizing:border-box;margin:0;padding:0}
html,body{width:1200px;height:2857px;overflow:hidden}
body{position:relative;font-family:"Roboto",sans-serif;color:var(--ink);background:var(--paper)}
.abs{position:absolute}
.topline{left:0;top:0;width:1200px;height:6px;background:var(--red)}
.header{left:0;top:6px;width:1200px;height:106px;background:var(--paper)}
.brand{display:flex;align-items:center;gap:10px;font-weight:900;color:var(--navy);text-transform:uppercase;line-height:1}
.brand-mark{width:26px;height:26px;border:4px solid currentColor}
.brand-name{font-size:22px;letter-spacing:.3px}
.header .brand{left:100px;top:32px}
.nav{left:368px;top:46px;font-size:15px;color:#333}
.nav a{color:inherit;text-decoration:none;position:absolute;white-space:nowrap}
.nav-sep{left:855px;top:36px;width:1px;height:40px;background:#ddd}
.call{left:874px;top:38px;display:flex;align-items:center;gap:12px;font-size:16px;font-weight:500;color:var(--ink);white-space:nowrap}
.call-icon{width:36px;height:36px;border:1px solid #bbb;border-radius:50%;display:flex;align-items:center;justify-content:center}

.hero{left:0;top:112px;width:1200px;height:650px;overflow:hidden}
.hero-photo{position:absolute;inset:0;background:linear-gradient(180deg,var(--hero-top) 0%,var(--hero-bottom) 100%)}
.hero-title{left:650px;top:135px;color:#fff;font-weight:500;font-size:43px;line-height:54px;text-transform:uppercase;white-space:nowrap}
.hero-sub{left:650px;top:258px;width:470px;color:#fff;font-style:italic;font-size:16px;line-height:28px}
.dots{left:652px;top:405px;display:flex;gap:6px}
.dots i{width:9px;height:9px;border-radius:50%;background:#fff;display:block}
.dots i.on{background:var(--red)}
.hero-cut{left:0;top:112px}

.choose h2{position:absolute;left:0;width:1200px;text-align:center;font-weight:700;font-size:30px;text-transform:uppercase;letter-spacing:.3px}
.choose .lead{top:772px;color:var(--ink)}
.choose .accent{top:822px;color:var(--red);font-weight:400;font-size:28px}
.choose p{position:absolute;left:200px;top:880px;width:800px;text-align:center;color:var(--soft);font-size:13px;line-height:27px}
.pill{position:absolute;top:973px;height:54px;border-radius:27px;border:2px solid var(--navy);color:var(--navy);font-size:14px;font-weight:700;text-transform:uppercase;display:flex;align-items:center;justify-content:center;white-space:nowrap}
.pill.primary{background:var(--red);border-color:var(--red);color:#fff}

.packages{left:0;top:1134px;width:1200px;height:708px;background:var(--navy)}
.packages h2{position:absolute;left:0;top:104px;width:1200px;text-align:center;color:#fff;font-family:"Roboto Condensed",sans-serif;font-size:30px;font-weight:700}
.card{position:absolute;top:197px;width:238px;height:399px;background:#fff;border-radius:3px;overflow:hidden}
.card-head{height:58px;background:#e5e5e5;display:flex;justify-content:space-between;align-items:center;padding:0 26px 0 27px;font-weight:700}
.card-title{color:var(--navy);font-size:18px;font-family:"Roboto Condensed",sans-serif}
.card-price{color:var(--red);font-size:16px}
.card ul{list-style:none;padding:0 8px}
.card li{position:relative;padding:12px 8px 12px 34px;font-size:13px;line-height:23px;color:#444;border-bottom:1px solid var(--line)}
.card li::before{content:"";position:absolute;left:12px;top:18px;width:8px;height:4px;border-left:2px solid var(--red);border-bottom:2px solid var(--red);transform:rotate(-45deg)}
.buy{position:absolute;left:62px;bottom:20px;width:114px;height:37px;border-radius:19px;background:var(--red);color:#fff;font-size:14px;font-weight:700;display:flex;align-items:center;justify-content:center}
.arrow{position:absolute;top:378px;width:38px;height:38px;border:2px solid #fff;border-radius:50%}

.subscribe{left:0;top:1842px;width:1200px;height:748px;background:var(--mist)}
.subscribe h2{position:absolute;left:0;top:84px;width:1200px;text-align:center;font-weight:500;font-size:26px;line-height:44px;color:#222;text-transform:uppercase}
.dotted{position:absolute;left:260px;width:680px;border-top:1px dotted #c9c9c9}
.feature{position:absolute;display:flex;align-items:center;gap:16px;width:420px}
.feature-icon{flex:none;width:80px;height:80px;border:2px solid var(--navy);border-radius:50%;display:flex;align-items:center;justify-content:center}
.feature p{font-size:14px;line-height:25px;color:#444}
.feature em{color:var(--red);font-style:normal}
.field{position:absolute;top:603px;height:52px;border-radius:26px;background:#fff;border:1px solid #ddd;font-size:14px;color:#888;display:flex;align-items:center;padding-left:32px}
.sub-btn{position:absolute;left:810px;top:603px;width:163px;height:52px;border-radius:26px;background:var(--red);color:#fff;font-size:16px;font-weight:700;display:flex;align-items:center;justify-content:center;text-transform:uppercase}

.footer{left:0;top:2590px;width:1200px;height:267px;background:var(--night);color:#fff}
.social{position:absolute;left:410px;top:64px;display:flex;gap:12px}
.social span{display:block;width:38px;height:38px;border:2px solid #fff;border-radius:50%}
.foot-links{position:absolute;left:160px;top:136px;font-size:16px;display:flex;gap:22px;white-space:nowrap}
.copy{position:absolute;left:0;top:186px;width:935px;text-align:center;font-size:11px;color:#ddd}
.foot-sep{position:absolute;left:710px;top:50px;width:1px;height:160px;background:#2f2f2f}
.footer .brand{position:absolute;left:766px;top:108px;color:#fff}
.footer .brand-name{font-size:28px}
.footer .brand-mark{width:32px;height:32px}
</style>
</head>
<body>
<div class="abs topline"></div>
<header class="abs header">
  <div class="abs brand"><span class="brand-mark"></span><span class="brand-name">Tally Porch<br>Helpers</span></div>
  <nav class="abs nav">
    <a style="left:0">How it works</a>
    <a style="left:126px">Service area</a>
    <a style="left:250px">Pricing</a>
    <a style="left:340px">About us</a>
    <a style="left:444px">Faq</a>
  </nav>
  <div class="abs nav-sep"></div>
  <div class="abs call">
    <span class="call-icon"><svg width="16" height="16" viewBox="0 0 24 24"><path fill="#221d80" d="M6.6 10.8a15.1 15.1 0 0 0 6.6 6.6l2.2-2.2c.3-.3.7-.4 1-.2 1.1.4 2.3.6 3.6.6.6 0 1 .4 1 1V20c0 .6-.4 1-1 1A17 17 0 0 1 3 4c0-.6.4-1 1-1h3.5c.6 0 1 .4 1 1 0 1.3.2 2.5.6 3.6.1.3 0 .7-.2 1z"/></svg></span>
    <span>Call Us : 1 555 010 2040</span>
  </div>
</header>

<section class="abs hero">
  <div class="hero-photo" role="img" aria-label="Hero photograph: open house yard sign on a front lawn"></div>
  <h1 class="abs hero-title">Tally Porch<br>Helpers</h1>
  <p class="abs hero-sub">Helping agents save time and money. We place signs and boost foot traffic to your open houses using proven marketing techniques.</p>
  <div class="abs dots"><i class="on"></i><i></i><i></i><i></i><i></i></div>
</section>
<svg class="abs hero-cut" width="1200" height="650" viewBox="0 0 1200 650">
  <polygon points="0,650 782,470 1200,650" fill="#fff"/>
  <polyline points="390,566 782,470 982,555" fill="none" stroke="#221d80" stroke-width="9" stroke-linejoin="miter"/>
  <path d="M772 515 l10-8 10 8 v10 h-20z" fill="none" stroke="#221d80" stroke-width="2"/>
  <circle cx="782" cy="518" r="2.5" fill="#221d80"/>
</svg>

<section class="choose">
  <h2 class="lead">Choose the option below that</h2>
  <h2 class="accent">Best describes you</h2>
  <p>Nemo enim ipsam voluptatem quia voluptas sit aspernatur aut odit aut fugit, sed quia consequuntur magni dolores eos qui ratione voluptatem sequi nesciunt quia non numquam eius modi tempora magnam aliquam quaerat voluptatem</p>
  <div class="pill primary" style="left:203px;width:239px">I'm a full on brokerage</div>
  <div class="pill" style="left:455px;width:273px">I'm an ind. broker with a team</div>
  <div class="pill" style="left:741px;width:256px">I need sign placement asap</div>
</section>

<section class="abs packages">
  <h2>OUR PACKAGES</h2>
  <div class="arrow" style="left:34px"><svg width="34" height="34" viewBox="0 0 34 34"><path d="M19 11l-6 6 6 6" fill="none" stroke="#fff" stroke-width="2.5"/></svg></div>
  <div class="arrow" style="left:1127px"><svg width="34" height="34" viewBox="0 0 34 34"><path d="M15 11l6 6-6 6" fill="none" stroke="#fff" stroke-width="2.5"/></svg></div>

  <div class="card" style="left:100px">
    <div class="card-head"><span class="card-title">5 SIGNS</span><span class="card-price">$79.9</span></div>
    <ul><li>Place signs strategically in best areas according to where the open house is located</li><li>Pick Up the signs after the open house</li><li>Store custom signs for you if needed</li></ul>
    <div class="buy">BUY NOW</div>
  </div>
  <div class="card" style="left:355px">
    <div class="card-head"><span class="card-title">10 SIGNS</span><span class="card-price">$79.9</span></div>
    <ul><li>Place signs strategically in best areas according to where the open house is located</li><li>Pick Up the signs after the open house</li><li>Store custom signs for you if needed</li></ul>
    <div class="buy">BUY NOW</div>
  </div>
  <div class="card" style="left:608px">
    <div class="card-head"><span class="card-title">15 SIGNS</span><span class="card-price">$79.9</span></div>
    <ul><li>Place signs strategically in best areas according to where the open house is located</li><li>Pick Up the signs after the open house</li><li>Store custom signs for you if needed</li></ul>
    <div class="buy">BUY NOW</div>
  </div>
  <div class="card" style="left:862px">
    <div class="card-head"><span class="card-title">20 SIGNS</span><span class="card-price">$79.9</span></div>
    <ul><li>Place signs strategically in best areas according to where the open house is located</li><li>Pick Up the signs after the open house</li><li>Store custom signs for you if needed</li></ul>
    <div class="buy">BUY NOW</div>
  </div>
</section>

<section class="abs subscribe">
  <h2>Sign up for a subscription and get these<br>marketing services for free</h2>
  <div class="dotted" style="top:216px"></div>
  <div class="feature" style="left:150px;top:274px">
    <span class="feature-icon"><svg width="40" height="40" viewBox="0 0 40 40" fill="none" stroke="#e3101f" stroke-width="2"><rect x="11" y="5" width="16" height="30" rx="2"/><rect x="18" y="10" width="14" height="8" rx="1"/><line x1="16" y1="30" x2="22" y2="30"/></svg></span>
    <p>Send <em>SMS</em> blast to your neighborhood informing them your home is for sale and if they know anyone looking to send them over</p>
  </div>
  <div class="feature" style="left:650px;top:274px">
    <span class="feature-icon"><svg width="40" height="40" viewBox="0 0 40 40" fill="none" stroke="#e3101f" stroke-width="2"><path d="M6 16l14-10 14 10v18H6z"/><path d="M6 16l14 10 14-10"/><rect x="12" y="11" width="16" height="10"/></svg></span>
    <p><em>Email</em> blast to your neighborhood informing them your home is for sale and if they know anyone looking to send them over</p>
  </div>
  <div class="feature" style="left:150px;top:404px">
    <span class="feature-icon"><svg width="40" height="40" viewBox="0 0 40 40" fill="none" stroke="#e3101f" stroke-width="2"><rect x="6" y="13" width="28" height="20" rx="2"/><path d="M15 6l5 7 5-7"/><rect x="10" y="17" width="16" height="12"/></svg></span>
    <p><em>Newsfeed</em> ads to people in your open house area</p>
  </div>
  <div class="feature" style="left:650px;top:404px">
    <span class="feature-icon"><svg width="40" height="40" viewBox="0 0 40 40" fill="none" stroke="#e3101f" stroke-width="2"><path d="M10 5h14l7 7v23H10z"/><path d="M24 5v7h7"/><rect x="14" y="20" width="12" height="8"/></svg></span>
    <p><em>VB blast</em> to your neighborhood informing them your home is for sale and if they know anyone looking to send them over</p>
  </div>
  <div class="dotted" style="top:541px"></div>
  <div class="field" style="left:228px;width:275px">Enter Name</div>
  <div class="field" style="left:518px;width:276px">Enter Email</div>
  <div class="sub-btn">Subscribe</div>
</section>

<footer class="abs footer">
  <div class="social">
    <span></span><span></span><span></span><span></span><span></span>
  </div>
  <div class="foot-links"><span>How it works</span><span>/</span><span>service</span><span>/</span><span>Pricing</span><span>/</span><span>About us</span><span>/</span><span>Faq</span></div>
  <p class="copy">Copyright © 2018, TALLY PORCH HELPERS All Rights Reserved.</p>
  <div class="foot-sep"></div>
  <div class="brand"><span class="brand-mark"></span><span class="brand-name">Tally Porch<br>Helpers</span></div>
</footer>
</body>
</html>
```